Ridgeline Orchards Organic Cherry POS card 7x11

We are wanting to create a one-sided 7 x 11 organic cherry card that is eye catching and informative.This should be clear and easy to read and not cluttered. We use these cards as a display in grocery stores, demo stands, and other events to market Organic Ridgeline Sweet Orchards. We have a few facts that we would like displayed on the card (see attachment).

Target Market(s)

Consumers

Industry/Entity Type

Agriculture

Requirements
Must have
• Natural color palettes
• Easy to read
• Ridgeline Orchards
Nice to have
• Unique, realistic cherry design

```html
<!DOCTYPE html>
<html lang="en">
<head>
<meta charset="utf-8">
<title>Ridgeline Orchards – Organic Cherry Card</title>
<link href="https://fonts.googleapis.com/css2?family=Lato:wght@400;700;900&family=Arimo:wght@700&display=swap" rel="stylesheet">
<style>
  :root {
    --paper: #ffffff;
    --ink: #1c1c1c;
    --band-dark: #17784f;
    --band-light: #33d69a;
    --band-rule: #3a1a1c;
    --berry-deep: #b8404c;
    --berry-mid: #d9606a;
    --berry-glow: #f27a80;
    --benefit-text: #fde2e6;
    --cherry-dark: #4a0a16;
    --cherry-red: #8e1626;
    --cherry-bright: #c0283a;
    --stem-green: #8fae3c;
  }
  * { margin: 0; padding: 0; box-sizing: border-box; }
  html, body { width: 764px; height: 1200px; overflow: hidden; background: var(--paper); }
  .card {
    position: relative;
    width: 764px;
    height: 1200px;
    overflow: hidden;
    font-family: "Lato", sans-serif;
    color: var(--ink);
  }
  .masthead {
    height: 326px;
    background: var(--paper);
    text-align: center;
  }
  .brand {
    display: flex;
    align-items: center;
    justify-content: center;
    gap: 16px;
    padding-top: 60px;
    height: 180px;
    font-weight: 700;
    font-size: 46px;
    color: var(--ink);
  }
  .brand-dot {
    width: 34px; height: 34px;
    border-radius: 50%;
    background: var(--cherry-red);
  }
  .fact-line {
    margin-top: 28px;
    font-size: 15px;
    font-weight: 400;
  }
  .headline-fact {
    margin-top: 14px;
    font-size: 20.5px;
    font-weight: 400;
    line-height: 31px;
    text-transform: uppercase;
    letter-spacing: 0.3px;
  }
  .benefits-band {
    height: 45px;
    background: linear-gradient(90deg, var(--band-dark) 0%, #22a872 45%, var(--band-light) 100%);
    border-bottom: 3px solid var(--band-rule);
    display: flex;
    align-items: center;
    justify-content: center;
  }
  .benefits-band h2 {
    font-weight: 900;
    font-size: 32px;
    letter-spacing: 13px;
    margin-right: -13px;
    color: #2a2a2a;
  }
  .benefits-panel {
    position: absolute;
    top: 371px; left: 0;
    width: 764px; height: 829px;
    background: radial-gradient(ellipse 60% 38% at 45% 38%, var(--berry-glow) 0%, var(--berry-mid) 55%, var(--berry-deep) 100%);
  }
  .benefit-list {
    list-style: none;
    text-align: center;
    padding-top: 25px;
    font-family: "Arimo", sans-serif;
    font-weight: 700;
    font-size: 43px;
    line-height: 60px;
    color: var(--benefit-text);
  }
  .cherry-photo {
    position: absolute;
    left: 0; bottom: 0;
    width: 764px; height: 490px;
    display: block;
  }
</style>
</head>
<body>
  <main class="card">
    <header class="masthead">
      <div class="brand"><span class="brand-dot"></span><span class="brand-name">Ridgeline Orchards</span></div>
      <p class="fact-line">Organic Ridgeline cherries make up 1/3 of the nation’s production.</p>
      <p class="headline-fact">Washington State is the nation’s<br>largest producer of organic cherries.</p>
    </header>
    <div class="benefits-band"><h2>HEALTH BENEFITS</h2></div>
    <section class="benefits-panel">
      <ul class="benefit-list">
        <li>Fat Free</li>
        <li>Source of VITAMIN C</li>
        <li>A Natural Anti-Inflammatory</li>
        <li>Source of POTASSIUM</li>
        <li>Source of MELATONIN</li>
      </ul>
      <svg class="cherry-photo" viewBox="0 0 764 490" role="img" aria-label="Photograph of a heap of glossy dark red sweet cherries with green stems">
        <defs>
          <linearGradient id="pileFill" x1="0" y1="0" x2="0" y2="1">
            <stop offset="0" stop-color="var(--cherry-bright)"/>
            <stop offset="0.4" stop-color="var(--cherry-red)"/>
            <stop offset="1" stop-color="var(--cherry-dark)"/>
          </linearGradient>
        </defs>
        <path d="M0 120 C 60 100, 120 80, 190 60 C 240 40, 280 10, 320 8 C 360 6, 400 30, 450 40 C 500 44, 540 40, 580 52 C 640 70, 700 100, 764 120 L 764 490 L 0 490 Z" fill="url(#pileFill)"/>
      </svg>
    </section>
  </main>
</body>
</html>
```